TALMORK

The business want a professional looking business card. We have a scetch we will add but want the extra upgrade, and would like more suggestions for variations of our business cards.

```html
<!DOCTYPE html>
<html lang="en">
<head>
<meta charset="utf-8">
<title>TALMORK – Business Card</title>
<link rel="stylesheet" href="https://fonts.googleapis.com/css2?family=Montserrat:wght@400;500;700&display=swap">
<style>
  :root {
    --page-bg: #141414;
    --card-bg: #1e1e1e;
    --card-back-bg: #1b1b1b;
    --gold: #c9a24c;
    --gold-line: #8a7035;
    --text-light: #f2f2f2;
    --pattern-dark: #141414;
    --pattern-light: #5a5a5a;
  }
  * { margin: 0; padding: 0; box-sizing: border-box; }
  html, body {
    width: 1200px;
    height: 1059px;
    overflow: hidden;
    background: var(--page-bg);
    font-family: "Montserrat", Arial, sans-serif;
  }
  .card {
    position: absolute;
    left: 255px;
    width: 690px;
    height: 392px;
    border-radius: 18px;
    overflow: hidden;
  }
  .card--front { top: 89px; background: var(--card-bg); }
  .card--back  { top: 546px; background: var(--card-back-bg); }

  .brand {
    position: absolute;
    text-align: center;
    color: var(--gold);
  }
  .brand__name {
    font-weight: 500;
    letter-spacing: 7px;
    line-height: 1;
  }
  .brand__tagline {
    font-weight: 500;
    letter-spacing: 3.5px;
    margin-top: 8px;
    line-height: 1;
  }
  .card--front .brand { left: 440px; width: 240px; top: 150px; }
  .card--front .brand__name { font-size: 25px; }
  .card--front .brand__tagline { font-size: 7.5px; }

  .holder { position: absolute; left: 38px; top: 176px; }
  .holder__name {
    color: var(--gold);
    font-weight: 700;
    font-size: 24px;
    line-height: 1.1;
  }
  .holder__role {
    color: var(--text-light);
    font-weight: 400;
    font-size: 19px;
    line-height: 1.3;
  }
  .divider {
    position: absolute;
    left: 38px;
    top: 244px;
    width: 611px;
    height: 1px;
    background: var(--gold-line);
  }
  .contacts {
    position: absolute;
    left: 38px;
    top: 258px;
    list-style: none;
  }
  .contacts__item {
    display: flex;
    align-items: center;
    height: 33.5px;
    color: var(--text-light);
    font-size: 19px;
    font-weight: 400;
  }
  .contacts__icon { width: 15px; height: 15px; margin-right: 10px; flex: none; }

  .back-pattern {
    position: absolute;
    inset: 0;
    background: linear-gradient(60deg, var(--pattern-dark) 0%, #202020 40%, #3a3a3a 70%, var(--pattern-light) 100%);
    opacity: 0.9;
  }
  .card--back .brand { left: 426px; width: 240px; top: 252px; }
  .card--back .brand__name { font-size: 21px; }
  .card--back .brand__tagline { font-size: 6.5px; margin-top: 7px; }
</style>
</head>
<body>
  <section class="card card--front">
    <div class="brand">
      <div class="brand__name">TALMORK</div>
      <div class="brand__tagline">SINCE 2026</div>
    </div>

    <div class="holder">
      <div class="holder__name">Henrik Aasvold Brenna</div>
      <div class="holder__role">CEO &amp; Founder</div>
    </div>

    <div class="divider"></div>

    <ul class="contacts">
      <li class="contacts__item">
        <svg class="contacts__icon" viewBox="0 0 16 16" aria-hidden="true">
          <path d="M3.5 1.5l2.5 3-1.5 1.5c.8 2 2.5 3.7 4.5 4.5l1.5-1.5 3 2.5-1.5 2.5C7 14 2 9 1 3z" fill="var(--gold)"/>
          <path d="M9 2a5 5 0 0 1 5 5M9 4.5a2.5 2.5 0 0 1 2.5 2.5" stroke="var(--gold)" stroke-width="1.2" fill="none"/>
        </svg>
        004791550372
      </li>
      <li class="contacts__item">
        <svg class="contacts__icon" viewBox="0 0 16 16" aria-hidden="true">
          <path d="M1 6l7-5 7 5v9H1z" fill="var(--gold)"/>
          <path d="M1 6l7 5 7-5" stroke="var(--card-bg)" stroke-width="1.2" fill="none"/>
        </svg>
        post@talmork.llc
      </li>
      <li class="contacts__item">
        <svg class="contacts__icon" viewBox="0 0 16 16" aria-hidden="true">
          <circle cx="8" cy="8" r="7" fill="var(--gold)"/>
          <path d="M4 4c2 1 1 3 3 3s1 3 0 5M10 3c1 2 3 2 4 4" stroke="var(--card-bg)" stroke-width="1.3" fill="none"/>
        </svg>
        www.talmork.llc
      </li>
    </ul>
  </section>

  <section class="card card--back">
    <div class="back-pattern" role="img" aria-label="Tone-on-tone repeating ornament pattern fading from black to silver grey"></div>
    <div class="brand">
      <div class="brand__name">TALMORK</div>
      <div class="brand__tagline">SINCE 2026</div>
    </div>
  </section>
</body>
</html>
```